Responsive OnePage Design for recruitment company

BrightHire is a modern company that sources interim people for its customers. Mostly developers, scrum master, project managers and designers. In this website we want to tell something about us, about how we work, our customers and we want our candidates be able to subscribe. The subscription form should be several fields (name, surname, email address, phone number and the possibility to upload your resume.We want it to fit into a existing wordpress plugin. We also want a listing of our job opportunities. The listing should be designed in a clear readable overview and if you click on the job you should get the details and be able to respond quickly by filling in you name, surname, email address, rate, phone number and upload your resume. We want this to be a standard configurable plugin. It should be easy to fill in the jobs in Wordpress by our administrator. We want a fresh, modern and cool design. It should be a responsive onepage design. If you click on a listed job you should stay on the same page. Our logo is added.

Target Market(s)

recruitment

Industry/Entity Type

Recruitment

Font styles to use
Sans Serif

Colors

Designer to choose colors to be used in the design.

Requirements
Must have
• Onepage design
• listing of job opportunities
• subscription forms
• be responsive

```html
<!DOCTYPE html>
<html lang="en">
<head>
<meta charset="utf-8">
<title>BrightHire – Interim Recruitment</title>
<link href="https://fonts.googleapis.com/css2?family=Montserrat:wght@400;500;600;700&family=Open+Sans:wght@400;600&display=swap" rel="stylesheet">
<style>
:root{
  --blue:#0d5bb5;
  --blue-dark:#0a3f8a;
  --blue-light:#1e8fd6;
  --ink:#1b2433;
  --text:#5b6270;
  --muted:#9aa0aa;
  --line:#e3e6ec;
  --grey-bg:#f3f4f8;
  --red:#e2335a;
  --white:#ffffff;
  --dark:#1d1f24;
  --client:#80858f;
}
*{box-sizing:border-box;margin:0;padding:0}
html,body{width:1200px;height:4036px;overflow:hidden}
body{position:relative;background:var(--white);font-family:'Open Sans',sans-serif;color:var(--text)}
.abs{position:absolute}
h2,h3,.brand,.nav a,.btn{font-family:'Montserrat',sans-serif}

/* header */
.site-header{position:absolute;left:0;top:0;width:1200px;height:86px;background:var(--white)}
.brand{position:absolute;left:172px;top:30px;font-size:22px;font-weight:600;letter-spacing:4px;color:var(--ink);text-transform:uppercase}
.brand span{color:var(--blue)}
.nav{position:absolute;right:172px;top:36px;display:flex;gap:24px}
.nav a{font-size:13px;font-weight:600;color:var(--ink);text-decoration:none;text-transform:uppercase}
.nav a.active{color:var(--blue)}

/* hero */
.hero-photo{position:absolute;left:0;top:86px;width:1200px;height:650px;background:linear-gradient(110deg,#c9d3dc 0%,#8d9aa8 35%,#3b4656 60%,#d7dde3 100%)}
.hero-caption{position:absolute;left:148px;top:296px;width:436px;height:202px;background:rgba(30,32,38,.72)}
.hero-caption h1{position:absolute;left:29px;top:48px;font-family:'Montserrat',sans-serif;color:var(--white);font-size:33px;line-height:46px;font-weight:700}
.dots{position:absolute;left:511px;top:638px;display:flex;gap:6px}
.dots i{display:block;width:40px;height:4px;background:rgba(255,255,255,.55)}
.dots i.on{background:var(--white)}

/* section titles */
.sec-title{position:absolute;left:0;width:1200px;text-align:center;font-size:32px;font-weight:500;color:var(--ink)}
.sec-title span{color:var(--blue)}
.sec-rule{position:absolute;left:560px;width:80px;height:3px;background:var(--blue)}
.sec-lead{position:absolute;left:300px;width:600px;text-align:center;font-size:12px;line-height:21px;color:var(--text)}

/* about */
.about-title{position:absolute;left:172px;top:818px;font-size:32px;font-weight:500;color:var(--ink)}
.about-title span{color:var(--blue)}
.about-rule{position:absolute;left:172px;top:866px;width:80px;height:3px;background:var(--blue)}
.about-text{position:absolute;left:172px;top:884px;width:370px;font-size:12px;line-height:19.5px}
.about-shadow{position:absolute;left:588px;top:808px;width:440px;height:340px;background:var(--blue)}
.about-photo{position:absolute;left:576px;top:796px;width:440px;height:340px;background:linear-gradient(135deg,#dfe7f0,#8fb0d4 55%,#4a6f9c)}
.play{position:absolute;left:766px;top:931px;width:60px;height:60px;border-radius:50%;border:2px solid rgba(255,255,255,.9)}
.play::after{content:"";position:absolute;left:23px;top:18px;border-left:18px solid var(--white);border-top:11px solid transparent;border-bottom:11px solid transparent}

/* how we work */
.how-band{position:absolute;left:0;top:1243px}
.step{position:absolute;width:220px;text-align:center}
.step-icon{width:97px;height:97px;margin:0 auto;border-radius:50%;border:5px solid var(--white);background:radial-gradient(circle,#f4f6f9 0%,#dbe4ef 60%,#b9cbe0 100%)}
.step h3{margin-top:22px;color:var(--white);font-size:16px;font-weight:600;text-transform:uppercase}
.step p{margin-top:12px;color:#dbe6f5;font-size:11.5px;line-height:20px}

/* jobs */
.jobs-bg{position:absolute;left:0;top:1880px}
.job{position:absolute;left:172px;width:856px;height:67px;background:var(--white);border:1px solid var(--line)}
.job h4{position:absolute;left:24px;top:15px;font-family:'Montserrat',sans-serif;font-size:15px;font-weight:600;color:var(--ink)}
.job .sub{position:absolute;left:24px;top:38px;font-size:11px;color:var(--muted)}
.job .loc{position:absolute;left:470px;top:24px;font-size:11.5px;color:var(--muted);display:flex;align-items:center;gap:7px}
.badge{position:absolute;left:720px;top:18px;width:92px;height:31px;border-radius:16px;border:1px solid var(--blue);color:var(--blue);font-family:'Montserrat',sans-serif;font-size:11px;font-weight:700;text-align:center;line-height:29px;text-transform:uppercase}
.badge.part{border-color:var(--red);color:var(--red)}
.pager{position:absolute;left:527px;top:2688px;display:flex;gap:8px}
.pager span{width:31px;height:31px;border-radius:50%;border:1px solid var(--line);background:var(--white);font-size:12px;color:var(--ink);text-align:center;line-height:29px}
.pager span.on{border-color:var(--blue);color:var(--blue)}

/* customers */
.client{position:absolute;transform:translate(-50%,-50%);font-family:'Montserrat',sans-serif;font-size:20px;font-weight:500;color:var(--client);white-space:nowrap}

/* footer */
.footer-photo{position:absolute;left:0;top:3320px;width:1200px;height:532px;background:linear-gradient(120deg,#2c2a28,#3c3733 40%,#24262b)}
.touch{position:absolute;left:172px;top:3468px;color:var(--white)}
.touch h3{font-size:24px;font-weight:600}
.contact{position:absolute;left:172px;color:var(--white);font-size:13px;line-height:24px}
.contact b{font-family:'Montserrat',sans-serif;font-weight:600;display:flex;align-items:center;gap:10px}
.contact p{padding-left:24px}
.subscribe{position:absolute;left:611px;top:3357px;width:417px;height:525px;background:linear-gradient(180deg,var(--blue-light),var(--blue) 45%,var(--blue-dark))}
.subscribe h3{position:absolute;left:0;top:40px;width:417px;text-align:center;color:var(--white);font-size:36px;font-weight:500}
.field{position:absolute;left:37px;width:345px;height:38px;border:1px solid rgba(255,255,255,.8);border-radius:19px;color:var(--white);font-size:13px;padding:10px 18px;display:flex;justify-content:space-between}
.field.area{height:86px;border-radius:14px}
.btn{position:absolute;left:37px;top:460px;width:345px;height:38px;border-radius:19px;background:var(--white);color:var(--blue);font-size:13px;font-weight:700;text-align:center;line-height:38px;text-transform:uppercase}
.social{position:absolute;top:3932px;width:40px;height:40px;background:var(--dark)}
.copyright{position:absolute;left:0;top:3992px;width:1200px;text-align:center;font-size:13px;color:var(--ink)}
</style>
</head>
<body>

<header class="site-header">
  <div class="brand">Bright<span>Hire</span></div>
  <nav class="nav">
    <a class="active" href="#home">Home</a>
    <a href="#about">About</a>
    <a href="#how">How We Work</a>
    <a href="#jobs">Job Opportunities</a>
    <a href="#customers">Customers</a>
    <a href="#contact">Contact</a>
  </nav>
</header>

<section id="home">
  <div class="hero-photo" role="img" aria-label="Recruiter in a suit interviewing a candidate in a bright office"></div>
  <div class="hero-caption"><h1>Find Your Dream Job.<br>Move up Today</h1></div>
  <div class="dots"><i></i><i class="on"></i><i></i><i></i></div>
  <svg class="abs" style="left:0;top:640px" width="1200" height="100"><polygon points="0,92 1200,4 1200,100 0,100" fill="#ffffff"/></svg>
</section>

<section id="about">
  <h2 class="about-title">About <span>BrightHire</span></h2>
  <div class="about-rule"></div>
  <p class="about-text">Sed ut perspiciatis unde omnis iste natus error sit voluptatem accusantium doloremque laudantium, totam rem aperiam, eaque ipsa quae ab illo inventore veritatis et quasi architecto beatae vitae dicta sunt explicabo. Nemo enim ipsam voluptatem quia voluptas sit aspernatur aut odit aut fugit, sed quia consequuntur magni dolores eos qui ratione voluptatem sequi nesciunt. Neque porro quisquam est, qui dolorem ipsum quia dolor sit amet, consectetur, adipisci velit, sed quia non numquam eius modi tempora incidunt ut labore et dolore magnam aliquam quaerat voluptatem. Neque porro quisquam est, qui dolorem ipsum quia dolor sit amet, consectetur, adipisci velit, sed quia non numquam eius.</p>
  <div class="about-shadow"></div>
  <div class="about-photo" role="img" aria-label="Team of colleagues gathered around a laptop in a meeting"></div>
  <div class="play"></div>
</section>

<section id="how">
  <svg class="how-band" width="1200" height="690"><polygon points="0,0 1200,102 1200,680 0,613" fill="#0d5bb5"/></svg>
  <h2 class="sec-title" style="top:1374px;color:#fff">How We Work</h2>
  <div class="sec-rule" style="top:1422px;background:#fff"></div>
  <p class="sec-lead" style="top:1438px;color:#dbe6f5">Sed ut perspiciatis unde omnis iste natus error sit voluptatem accusantium doloremque laudantium, totam rem aperiam, eaque ipsa quae ab illo inventore veritatis et quasi architecto beatae vit</p>
  <div class="step" style="left:151px;top:1538px"><div class="step-icon" role="img" aria-label="Clipboard with pencils"></div><h3>Register</h3><p>Sed ut perspiciatis unde omni natus error sit voluptatem accusa ntium doloremque laudantium, tot am rem aperiam, eaque ipsa.</p></div>
  <div class="step" style="left:377px;top:1538px"><div class="step-icon" role="img" aria-label="Profile avatar"></div><h3>Upload Profile</h3><p>Sed ut perspiciatis unde omni natus error sit voluptatem accusa ntium doloremque laudantium, tot am rem aperiam, eaque ipsa.</p></div>
  <div class="step" style="left:603px;top:1538px"><div class="step-icon" role="img" aria-label="Magnifying glass"></div><h3>Search Jobs</h3><p>Sed ut perspiciatis unde omni natus error sit voluptatem accusa ntium doloremque laudantium, tot am rem aperiam, eaque ipsa.</p></div>
  <div class="step" style="left:829px;top:1538px"><div class="step-icon" role="img" aria-label="Paper plane"></div><h3>Apply Jobs</h3><p>Sed ut perspiciatis unde omni natus error sit voluptatem accusa ntium doloremque laudantium, tot am rem aperiam, eaque ipsa.</p></div>
</section>

<section id="jobs">
  <svg class="jobs-bg" width="1200" height="980" style="z-index:-1"><polygon points="0,0 1200,40 1200,900 0,980" fill="#f3f4f8"/></svg>
  <h2 class="sec-title" style="top:1984px">Job <span>Opportunities</span></h2>
  <div class="sec-rule" style="top:2032px"></div>
  <p class="sec-lead" style="top:2048px">Sed ut perspiciatis unde omnis iste natus error sit voluptatem accusantium doloremque laudantium, totam rem aperiam, eaque ipsa quae ab illo inventore veritatis et quasi architecto beatae vit</p>

  <div class="job" style="top:2128px"><h4>Developers</h4><span class="sub">Sed utaperiam, eaque ipsa quaecto beatae vit</span><span class="loc"><svg width="9" height="12" viewBox="0 0 9 12"><path d="M4.5 0A4.5 4.5 0 0 0 0 4.5C0 8 4.5 12 4.5 12S9 8 9 4.5A4.5 4.5 0 0 0 4.5 0zm0 6.3a1.8 1.8 0 1 1 0-3.6 1.8 1.8 0 0 1 0 3.6z" fill="#9aa0aa"/></svg>Location Name, City Name</span><span class="badge">Full Time</span></div>
  <div class="job" style="top:2203px"><h4>Scrum master</h4><span class="sub">Sed utaperiam, eaque ipsa quaecto beatae vit</span><span class="loc"><svg width="9" height="12" viewBox="0 0 9 12"><path d="M4.5 0A4.5 4.5 0 0 0 0 4.5C0 8 4.5 12 4.5 12S9 8 9 4.5A4.5 4.5 0 0 0 4.5 0zm0 6.3a1.8 1.8 0 1 1 0-3.6 1.8 1.8 0 0 1 0 3.6z" fill="#9aa0aa"/></svg>Location Name, City Name</span><span class="badge part">Part Time</span></div>
  <div class="job" style="top:2278px"><h4>Project managers</h4><span class="sub">Sed utaperiam, eaque ipsa quaecto beatae vit</span><span class="loc"><svg width="9" height="12" viewBox="0 0 9 12"><path d="M4.5 0A4.5 4.5 0 0 0 0 4.5C0 8 4.5 12 4.5 12S9 8 9 4.5A4.5 4.5 0 0 0 4.5 0zm0 6.3a1.8 1.8 0 1 1 0-3.6 1.8 1.8 0 0 1 0 3.6z" fill="#9aa0aa"/></svg>Location Name, City Name</span><span class="badge">Full Time</span></div>
  <div class="job" style="top:2353px"><h4>Developers</h4><span class="sub">Sed utaperiam, eaque ipsa quaecto beatae vit</span><span class="loc"><svg width="9" height="12" viewBox="0 0 9 12"><path d="M4.5 0A4.5 4.5 0 0 0 0 4.5C0 8 4.5 12 4.5 12S9 8 9 4.5A4.5 4.5 0 0 0 4.5 0zm0 6.3a1.8 1.8 0 1 1 0-3.6 1.8 1.8 0 0 1 0 3.6z" fill="#9aa0aa"/></svg>Location Name, City Name</span><span class="badge part">Part Time</span></div>
  <div class="job" style="top:2428px"><h4>Scrum master</h4><span class="sub">Sed utaperiam, eaque ipsa quaecto beatae vit</span><span class="loc"><svg width="9" height="12" viewBox="0 0 9 12"><path d="M4.5 0A4.5 4.5 0 0 0 0 4.5C0 8 4.5 12 4.5 12S9 8 9 4.5A4.5 4.5 0 0 0 4.5 0zm0 6.3a1.8 1.8 0 1 1 0-3.6 1.8 1.8 0 0 1 0 3.6z" fill="#9aa0aa"/></svg>Location Name, City Name</span><span class="badge">Full Time</span></div>
  <div class="job" style="top:2503px"><h4>Designers</h4><span class="sub">Sed utaperiam, eaque ipsa quaecto beatae vit</span><span class="loc"><svg width="9" height="12" viewBox="0 0 9 12"><path d="M4.5 0A4.5 4.5 0 0 0 0 4.5C0 8 4.5 12 4.5 12S9 8 9 4.5A4.5 4.5 0 0 0 4.5 0zm0 6.3a1.8 1.8 0 1 1 0-3.6 1.8 1.8 0 0 1 0 3.6z" fill="#9aa0aa"/></svg>Location Name, City Name</span><span class="badge">Full Time</span></div>
  <div class="job" style="top:2578px"><h4>Project managers</h4><span class="sub">Sed utaperiam, eaque ipsa quaecto beatae vit</span><span class="loc"><svg width="9" height="12" viewBox="0 0 9 12"><path d="M4.5 0A4.5 4.5 0 0 0 0 4.5C0 8 4.5 12 4.5 12S9 8 9 4.5A4.5 4.5 0 0 0 4.5 0zm0 6.3a1.8 1.8 0 1 1 0-3.6 1.8 1.8 0 0 1 0 3.6z" fill="#9aa0aa"/></svg>Location Name, City Name</span><span class="badge part">Part Time</span></div>

  <div class="pager"><span class="on">1</span><span>2</span><span>3</span><span>4</span></div>
</section>

<section id="customers">
  <h2 class="sec-title" style="top:2930px">Our <span>Customers</span></h2>
  <div class="sec-rule" style="top:2978px"></div>
  <p class="sec-lead" style="top:2994px">Sed ut perspiciatis unde omnis iste natus error sit voluptatem accusantium doloremque laudantium, totam rem aperiam, eaque ipsa quae ab illo inventore veritatis et quasi architecto beatae vit</p>
  <div class="client" style="left:380px;top:3105px">Norvale</div>
  <div class="client" style="left:522px;top:3105px">Tessara</div>
  <div class="client" style="left:660px;top:3105px">Lumenco</div>
  <div class="client" style="left:800px;top:3105px">Vantor</div>
  <div class="client" style="left:372px;top:3193px">Bexford</div>
  <div class="client" style="left:482px;top:3193px">Solmi</div>
  <div class="client" style="left:596px;top:3193px">Dunmore</div>
  <div class="client" style="left:740px;top:3193px">Kestrel</div>
</section>

<section id="contact">
  <div class="footer-photo" role="img" aria-label="Business handshake in a dim office"></div>
  <svg class="abs" style="left:0;top:3310px" width="1200" height="80"><polygon points="0,0 1200,0 1200,70 600,22 0,24" fill="#ffffff"/></svg>
  <div class="touch"><h3>Get In Touch</h3></div>
  <div class="contact" style="top:3524px"><b><svg width="10" height="13" viewBox="0 0 9 12"><path d="M4.5 0A4.5 4.5 0 0 0 0 4.5C0 8 4.5 12 4.5 12S9 8 9 4.5A4.5 4.5 0 0 0 4.5 0zm0 6.3a1.8 1.8 0 1 1 0-3.6 1.8 1.8 0 0 1 0 3.6z" fill="#fff"/></svg>Address:</b><p>48 Maple Street<br>Riverton, TX 75010</p></div>
  <div class="contact" style="top:3621px"><b><svg width="12" height="12" viewBox="0 0 12 12"><path d="M2.4 0l2 2.6-1.1 1.6a8 8 0 0 0 4.5 4.5l1.6-1.1L12 9.6 10.4 12C4.8 11.6.4 7.2 0 1.6z" fill="#fff"/></svg>Phone Number:</b><p>Phone: (555) 010-2486</p></div>
  <div class="contact" style="top:3694px"><b><svg width="12" height="10" viewBox="0 0 12 10"><path d="M0 0h12v10H0z" fill="#fff"/><path d="M0 0l6 5 6-5" stroke="#333" fill="none"/></svg>Email Address:</b><p>hello@brighthire.example</p></div>

  <form class="subscribe">
    <h3>Subscription</h3>
    <div class="field" style="top:128px">Name</div>
    <div class="field" style="top:174px">Surname</div>
    <div class="field" style="top:220px">Email</div>
    <div class="field" style="top:266px">Phone</div>
    <div class="field area" style="top:312px">Address</div>
    <div class="field" style="top:408px">Upload your resume<svg width="14" height="14" viewBox="0 0 14 14"><path d="M7 0v8M3.5 4.5L7 8l3.5-3.5M1 10v3h12v-3" stroke="#fff" stroke-width="2" fill="none"/></svg></div>
    <div class="btn">Submit Here</div>
  </form>

  <div class="social" style="left:538px" aria-label="Social network one"></div>
  <div class="social" style="left:586px" aria-label="Social network two"></div>
  <div class="social" style="left:634px" aria-label="Social network three"></div>
  <p class="copyright">© 2019 BrightHire, All Rights Are Reserved Terms of Use | Privacy Policy</p>
</section>

</body>
</html>
```